Corven Hale Interiors Web Site

We are looking at web site for our start-up company which is located in Abu Dhabi United Arab Emirates. Our main business activity is Interior fit out for high medium to high end projects in residential, corporate and hospitality.
In terms of look and feel the web site should be vibrant yet professional reflecting the artistic/construction nature of our business and built along or allows the following aspects:
- Number of Pages: 8-10 main pages (Including 10 Sub Pages)
- A custom responsive web design compatible with all browsers
- Dynamic (admin panel). CMS
- Anti Spam Online Forms
- Photo & Video Gallery
- Mobile Ready (Iphone,Android)]
- Social Media Integration
- Google Map
- Banner Artworks

```html
<!DOCTYPE html>
<html lang="en">
<head>
<meta charset="utf-8">
<title>Corven Hale Interiors</title>
<link rel="stylesheet" href="https://fonts.googleapis.com/css2?family=Open+Sans:wght@300;400;600;700&display=swap">
<style>
:root{
  --teal-dark:#1c3b4a;
  --teal:#1f4c5e;
  --teal-accent:#2b6a82;
  --link-blue:#8fc6e0;
  --ink:#222a30;
  --grey:#8d9398;
  --grey-mid:#555b60;
  --line:#e2e5e7;
  --white:#ffffff;
  --map-land:#e9e5dc;
  --map-water:#a8c4de;
}
*{box-sizing:border-box;margin:0;padding:0}
html,body{width:1200px;height:2365px;overflow:hidden}
body{font-family:"Open Sans",sans-serif;color:var(--ink);background:var(--white);position:relative}

.top-bar{position:absolute;left:0;top:0;width:1200px;height:57px;background:var(--teal-dark);color:var(--white);font-size:12px}
.top-bar .item{position:absolute;top:20px;display:flex;align-items:center;gap:8px}
.top-bar svg{width:11px;height:11px;fill:var(--white)}

.hero{position:absolute;left:0;top:57px;width:1200px;height:684px;
  background:linear-gradient(180deg,rgba(0,0,0,0) 55%,rgba(0,0,0,.35) 100%),
  linear-gradient(90deg,#27282b 0%,#3a3c40 30%,#6e7276 55%,#b7c2c8 78%,#d6e2e8 100%)}
.hero-title{position:absolute;left:0;width:1200px;text-align:center;color:var(--white)}
.hero-title .big{position:absolute;top:470px;width:100%;font-size:60px;font-weight:700;letter-spacing:1px}
.hero-title .sub{position:absolute;top:540px;width:100%;font-size:56px;font-weight:300}
.hero-dots{position:absolute;top:626px;left:557px;display:flex;gap:5px}
.hero-dots span{width:17px;height:17px;border:2px solid var(--white);border-radius:50%}
.hero-dots span.active{background:#9fb7c6}

.nav{position:absolute;left:402px;top:57px;width:798px;height:113px;background:rgba(35,35,37,.82)}
.nav a{position:absolute;top:44px;color:var(--white);text-decoration:none;font-size:16px;font-weight:600;transform:translateX(-50%)}
.nav a.current{color:var(--link-blue)}
.nav a.current::after{content:"";position:absolute;left:0;right:0;bottom:-9px;height:2px;background:var(--link-blue)}

.brand{position:absolute;left:131px;top:0;width:271px;height:232px}
.brand svg{position:absolute;inset:0}
.brand .mark{position:absolute;left:113px;top:14px;width:46px;height:46px;background:var(--teal)}
.brand .name{position:absolute;top:82px;width:100%;text-align:center;color:var(--ink);font-weight:600;line-height:1}
.brand .name .l1{display:block;font-size:32px}
.brand .name .l2{display:block;font-size:15px;letter-spacing:7px;margin-top:14px}

.welcome{position:absolute;top:741px;left:0;width:1200px;height:202px;text-align:center;border-bottom:1px solid var(--line)}
.welcome h1{position:absolute;top:32px;width:100%;font-size:35px;font-weight:700}
.welcome h1 span{font-weight:400;color:var(--teal)}
.welcome .lead{position:absolute;top:82px;width:100%;font-size:20px;color:var(--grey-mid)}
.welcome .small{position:absolute;top:126px;width:100%;font-size:13px;line-height:23px;color:var(--grey)}

.services{position:absolute;top:943px;left:0;width:1200px;height:554px}
.service{position:absolute;top:0;width:295px}
.service h2{position:absolute;top:22px;font-size:34px;font-weight:400;color:var(--teal)}
.service .photo{position:absolute;top:84px;width:295px;height:219px;border:1px solid #d7dadc;padding:4px;background:var(--white)}
.service .photo div{width:100%;height:100%}
.service h3{position:absolute;top:320px;font-size:19px;font-weight:400;color:var(--ink)}
.service p{position:absolute;top:357px;width:295px;font-size:13px;line-height:22px;color:var(--grey)}
.btn{position:absolute;top:442px;width:121px;height:52px;background:var(--teal-dark);color:var(--white);font-size:16px;line-height:52px;text-align:center;border-radius:2px}

.gallery{position:absolute;top:1497px;left:0;width:1200px;height:468px;
  background:radial-gradient(ellipse at 50% 45%,#5a5652 0%,#3e3b38 60%,#2d2b29 100%)}
.gallery h2{position:absolute;top:32px;width:100%;text-align:center;font-size:32px;color:var(--white);font-weight:400}
.gallery h2 b{font-weight:700}
.gallery .lead{position:absolute;top:87px;width:100%;text-align:center;font-size:20px;color:#e9e9e9}
.thumb{position:absolute;top:148px;width:222px;height:216px;border:3px solid #d9d9d9}
.thumb .play{position:absolute;left:87px;top:84px;width:48px;height:48px}
.gallery .arrows{position:absolute;top:410px;left:588px;display:flex;gap:6px}

.map{position:absolute;top:1965px;left:0;width:1200px;height:317px;
  background:linear-gradient(100deg,var(--map-water) 0%,#b9cfe2 22%,var(--map-land) 34%,#eceae3 70%,#dfe6d8 100%)}
.map-link{position:absolute;left:11px;top:13px;width:148px;height:28px;background:var(--white);font-size:12px;line-height:28px;text-align:center;color:#3a6fb0;box-shadow:0 1px 3px rgba(0,0,0,.3)}
.pin{position:absolute;left:792px;top:178px;width:24px;height:36px}
.contact-card{position:absolute;left:817px;top:69px;width:200px;height:150px;background:var(--white);box-shadow:0 2px 6px rgba(0,0,0,.25);padding:22px 18px}
.contact-card .who{font-size:15px;color:var(--ink)}
.contact-card .role{font-size:9px;color:var(--grey);margin-bottom:12px}
.contact-card .lines{font-size:8px;line-height:11px;color:var(--grey-mid)}

.footer{position:absolute;top:2282px;left:0;width:1200px;height:83px;background:var(--teal-dark);color:var(--white)}
.footer .legal{position:absolute;left:131px;top:32px;font-size:12px;display:flex;gap:14px}
.footer .social{position:absolute;left:935px;top:22px;display:flex;gap:9px}
.footer .social span{width:36px;height:36px;border:2px solid var(--white);border-radius:50%;display:flex;align-items:center;justify-content:center}
</style>
</head>
<body>

<header class="top-bar">
  <div class="item" style="left:530px"><svg viewBox="0 0 10 10"><path d="M5 0a3.5 3.5 0 0 0-3.5 3.5C1.5 6 5 10 5 10s3.5-4 3.5-6.5A3.5 3.5 0 0 0 5 0zm0 5a1.4 1.4 0 1 1 0-2.8A1.4 1.4 0 0 1 5 5z"/></svg>P.O. Box 2187 Abu Dhabi-UAE</div>
  <div class="item" style="left:754px"><svg viewBox="0 0 10 10"><path d="M2 0l2 2.5-1 1.2a6 6 0 0 0 3.3 3.3l1.2-1L10 8l-1.5 2C4 10 0 6 0 1.5z"/></svg>Phone: 971 50 418 2263</div>
  <div class="item" style="left:926px"><svg viewBox="0 0 10 8"><path d="M0 0h10v1L5 4 0 1zM0 2l5 3 5-3v6H0z"/></svg>Email: info@corvenhale.ae</div>
</header>

<section class="hero" role="img" aria-label="Living room with two white armchairs, a glass coffee table, patterned wall and bright windows">
  <div class="hero-title">
    <div class="big">CORVEN HALE</div>
    <div class="sub">Interior Decorating Company</div>
  </div>
  <div class="hero-dots"><span></span><span class="active"></span><span></span><span></span></div>
</section>

<nav class="nav">
  <a class="current" style="left:128px">Home</a>
  <a style="left:221px">About</a>
  <a style="left:319px">Services</a>
  <a style="left:478px">Photo &amp; Video Gallery</a>
  <a style="left:656px">Contacts</a>
</nav>

<div class="brand">
  <svg viewBox="0 0 271 232" width="271" height="232"><polygon points="0,0 271,0 271,198 135.5,228 0,198" fill="#fff" stroke="#1c3b4a" stroke-width="4"/></svg>
  <div class="mark"></div>
  <div class="name"><span class="l1">Corven Hale</span><span class="l2">INTERIORS</span></div>
</div>

<section class="welcome">
  <h1>Welcome! To <span>Corven Hale</span></h1>
  <p class="lead">Desorporis suscipit labornisi ut aliquid ex ea commodi consequatuis autem reprehenderies</p>
  <p class="small">Lorem ipsum dolor sit amet, consectetur adipisicing elit, sed do eiusmod tempor incididunt ut labore et dolore magna aliqua.<br>Ut enim ad minim veniam, quis nostrud exercitation ullamco laboris nisi ut aliquip</p>
</section>

<section class="services">
  <article class="service" style="left:131px">
    <h2>Hotel</h2>
    <div class="photo"><div role="img" aria-label="Modern hotel lounge with green feature wall" style="background:linear-gradient(160deg,#e8ecea 0%,#b8c98a 45%,#d9dcd8 75%,#9a9c98 100%)"></div></div>
    <h3>Neriuase bertyuasa deloertyas</h3>
    <p>Lorem ipsum dolor sit amet, consectetur adipisicing elit, sed do eiusmod tempor incididunt ut labore et dolore magna aliqua.</p>
    <div class="btn">READ MORE</div>
  </article>
  <article class="service" style="left:451px">
    <h2>Rooms</h2>
    <div class="photo"><div role="img" aria-label="Bedroom with canopy bed and chandelier" style="background:linear-gradient(160deg,#efe9e4 0%,#d8c6bf 40%,#b69a8e 70%,#e4ddd6 100%)"></div></div>
    <h3>Neriuase bertyuasa deloertyas</h3>
    <p>Lorem ipsum dolor sit amet, consectetur adipisicing elit, sed do eiusmod tempor incididunt ut labore et dolore magna aliqua.</p>
    <div class="btn">READ MORE</div>
  </article>
  <article class="service" style="left:771px">
    <h2>Bathrooms</h2>
    <div class="photo"><div role="img" aria-label="Warm living room with fireplace and sofas" style="background:linear-gradient(160deg,#c69a74 0%,#e9dccb 40%,#a8502c 75%,#d8cab8 100%)"></div></div>
    <h3>Neriuase bertyuasa deloertyas</h3>
    <p>Lorem ipsum dolor sit amet, consectetur adipisicing elit, sed do eiusmod tempor incididunt ut labore et dolore magna aliqua.</p>
    <div class="btn">READ MORE</div>
  </article>
</section>

<section class="gallery" role="img" aria-label="Dim lounge interior behind the gallery">
  <h2><b>Photo &amp; Video</b> Gallery</h2>
  <p class="lead">Desorporis suscipit labornisi ut aliquid ex ea commodi consequatuis autem reprehenderies</p>
  <div class="thumb" style="left:131px" role="img" aria-label="Dining room with set table" aria-hidden="false"><div style="width:100%;height:100%;background:linear-gradient(165deg,#d9d4cc 0%,#a88f72 50%,#6a4e3a 100%)"></div></div>
  <div class="thumb" style="left:371px" role="img" aria-label="Video: living room with green sofas"><div style="width:100%;height:100%;background:linear-gradient(165deg,#dad8a8 0%,#b8c07a 45%,#3f8a3a 100%)"></div>
    <svg class="play" viewBox="0 0 48 48"><circle cx="24" cy="24" r="22" fill="none" stroke="#fff" stroke-width="3"/><polygon points="19,14 35,24 19,34" fill="#fff"/></svg></div>
  <div class="thumb" style="left:610px" role="img" aria-label="Terrace with red loungers overlooking hills"><div style="width:100%;height:100%;background:linear-gradient(180deg,#c8d8e6 0%,#7f9a6a 50%,#b8b2a8 75%,#8a8580 100%)"></div></div>
  <div class="thumb" style="left:847px" role="img" aria-label="Video: striped wall with teal sofa"><div style="width:100%;height:100%;background:linear-gradient(165deg,#5a7a86 0%,#3f6470 55%,#4f8a8a 100%)"></div>
    <svg class="play" viewBox="0 0 48 48"><circle cx="24" cy="24" r="22" fill="none" stroke="#fff" stroke-width="3"/><polygon points="19,14 35,24 19,34" fill="#fff"/></svg></div>
  <div class="arrows">
    <svg width="18" height="26" viewBox="0 0 18 26"><polyline points="14,3 4,13 14,23" fill="none" stroke="#bdbdbd" stroke-width="4"/></svg>
    <svg width="18" height="26" viewBox="0 0 18 26"><polyline points="4,3 14,13 4,23" fill="none" stroke="#bdbdbd" stroke-width="4"/></svg>
  </div>
</section>

<section class="map" role="img" aria-label="Street map of the office location">
  <div class="map-link">View on City Map</div>
  <div class="contact-card">
    <div class="who">Samir Haddad</div>
    <div class="role">Business Owner</div>
    <div class="lines">P.O.Box 2187 Abu Dhabi - UAE<br>Tel: +971 2 555 0148<br>Fax: +971 2 555 0149<br>Mobile: +971 50 418 2263<br>samir@corvenhale.ae<br>www.corvenhale.ae</div>
  </div>
  <svg class="pin" viewBox="0 0 24 36"><path d="M12 0A12 12 0 0 0 0 12c0 9 12 24 12 24s12-15 12-24A12 12 0 0 0 12 0z" fill="#3a3a3a"/><circle cx="12" cy="12" r="4" fill="#e9e5dc"/></svg>
</section>

<footer class="footer">
  <div class="legal"><span>Privacy Policy</span><span>|</span><span>Terms and Conditions</span><span>|</span><span>© Company LLC 2014</span></div>
  <div class="social">
    <span><svg width="16" height="12" viewBox="0 0 10 8"><path d="M0 0h10v1L5 4 0 1zM0 2l5 3 5-3v6H0z" fill="#fff"/></svg></span>
    <span></span>
    <span></span>
  </div>
</footer>

</body>
</html>
```